New Organic Skin Care Line Needs to Design a Product Label

***THE WINNER OF THIS PROJECT WILL MOST LIKELY BECOME THE EXCLUSIVE DESIGNER FOR OUR OTHER PRODUCT LABELS***

We need a label design for a new organic skin care product line called "Maple Dew Gala." This specific product is a 100% pure organic coconut oil. It's used for skin hydration, protection, and makeup removal.

Info to include on front label:

1. Logo: Maple Dew Gala (attached)
2. Product Name: Pure Coconut Oil (emphasize "organic" somewhere)
3. Slogan: Hydrate your skin and hair.
4. Size: 8 FL OZ 236mL

Attached is:

1. The brand logo "Maple Dew Gala" with a white background.
2. An image of the bottle we will use.
3. An image of the bottle with lines to show the size and placement of the label.
4. The brand logo "Maple Dew Gala" with a black background. (photoshop file)

What we need:

A simple mock up of the front side of the label on the bottle. We first want to know what it will look like on the bottle given the size and dimensions.

- We would like one label with a white background (including the logo with a white background).
- We would like a second label with a black background (including the logo with a black background, just need to make the black font white instead of black).

We can get a great idea of what to expect from the front side of the label so we will complete the back side once we identify a winner.
Updates

Apologies, but we are now using a different bottle. The previous one is now discontinued. Please view the two most recent images uploaded. One is an image of the new bottle by itself. The other is an image of that bottle with instructions. Please use your most recent designs on the new bottle. Feel free to make any modifications you see fit to compliment the new bottle shape. Added Friday, March 18, 2016

Reason: We are still working with the label company to finalize the size. Once the size is confirmed we will have to tweak labels based on finalized measurements.

Target Market(s)

Women, 18-70

Industry/Entity Type

Skin Care Product

Font styles to use
Decorative
Script

Requirements
Must have
• -"shabby sheek" and "cute" theme
• -soft organic feel
• -the ingredients are organic, pure, and natural. That should be an essence of the label.

```html
<!DOCTYPE html>
<html lang="en">
<head>
<meta charset="utf-8">
<title>Maple Dew Gala – Pure Coconut Oil Label</title>
<link rel="stylesheet" href="https://fonts.googleapis.com/css2?family=Cinzel:wght@400;600&family=Crimson+Text:wght@400;600&display=swap">
<style>
  :root {
    --canvas: #f4f4f2;
    --label: #ffffff;
    --ink: #1a1a1a;
    --edge: #b9b9b9;
    --brand-pink: #e8337a;
    --leaf-green: #9bbb1e;
    --coconut-brown: #8a6a45;
    --coconut-cream: #f3eee4;
    --palm-green: #4f7a3a;
  }
  * { margin: 0; padding: 0; box-sizing: border-box; }
  html, body {
    width: 716px;
    height: 1200px;
    overflow: hidden;
    background: var(--canvas);
  }
  .label {
    position: absolute;
    left: 29px;
    top: 288px;
    width: 658px;
    height: 624px;
  }
  .label svg { width: 100%; height: 100%; display: block; }
  .label-body { fill: var(--label); stroke: var(--edge); stroke-width: 1; }
  .label-rule { fill: none; stroke: var(--ink); stroke-width: 4; stroke-linejoin: round; }
  .divider { stroke: var(--ink); stroke-width: 3; }
  .organic-flourish { fill: none; stroke: var(--leaf-green); stroke-width: 2; stroke-linecap: round; }
  .brand-name {
    font-family: "Cinzel", serif;
    font-size: 19px;
    letter-spacing: 2px;
    fill: var(--brand-pink);
  }
  .product-name {
    font-family: "Cinzel", serif;
    font-weight: 600;
    font-size: 17px;
    letter-spacing: 1px;
    fill: var(--ink);
  }
  .slogan {
    font-family: "Crimson Text", serif;
    font-weight: 600;
    font-size: 9.5px;
    letter-spacing: 0.3px;
    fill: var(--ink);
  }
  .organic {
    font-family: "Crimson Text", serif;
    font-size: 15px;
    fill: var(--leaf-green);
  }
  .size {
    font-family: "Crimson Text", serif;
    font-size: 11px;
    fill: var(--ink);
  }
</style>
</head>
<body>
  <div class="label">
    <svg viewBox="-8 -8 430 416" xmlns="http://www.w3.org/2000/svg">
      <defs>
        <linearGradient id="coconut-tones" x1="0" y1="0" x2="1" y2="1">
          <stop offset="0" stop-color="var(--palm-green)"/>
          <stop offset="0.45" stop-color="var(--coconut-cream)"/>
          <stop offset="1" stop-color="var(--coconut-brown)"/>
        </linearGradient>
      </defs>

      <!-- label die-cut shape -->
      <path class="label-body" d="M207,4 C222,30 262,48 300,85 C338,122 352,170 352,214 L414,214 L414,288 L372,288 C370,355 300,404 207,404 C114,404 44,355 42,288 L0,288 L0,214 L62,214 C62,170 76,122 114,85 C152,48 192,30 207,4 Z"/>

      <!-- dome and bowl border rules -->
      <path class="label-rule" d="M0,222 L70,222 C70,175 84,130 120,94 C156,58 194,40 207,18 C220,40 258,58 294,94 C330,130 344,175 344,222 L414,222"/>
      <path class="label-rule" d="M0,280 L50,280 C52,345 120,392 207,392 C294,392 362,345 364,280 L414,280"/>

      <!-- brand name -->
      <circle cx="207" cy="140" r="5" fill="var(--brand-pink)"/>
      <text class="brand-name" x="207" y="180" text-anchor="middle">MAPLE DEW GALA</text>

      <!-- coconut illustration area -->
      <rect x="142" y="196" width="130" height="60" rx="6" fill="url(#coconut-tones)" role="img" aria-label="Illustration of halved coconuts with leaves and palm fronds"/>

      <line class="divider" x1="100" y1="266" x2="314" y2="266"/>

      <text class="product-name" x="207" y="289" text-anchor="middle">PURE COCONUT OIL</text>
      <text class="slogan" x="207" y="321" text-anchor="middle">HYDRATE YOUR SKIN AND HAIR</text>

      <path class="organic-flourish" d="M108,350 q10,-4 20,0 t20,0 t16,-1"/>
      <text class="organic" x="207" y="355" text-anchor="middle">ORGANIC</text>
      <path class="organic-flourish" d="M250,349 q10,-4 20,0 t20,0 t16,1"/>

      <text class="size" x="207" y="382" text-anchor="middle">236 ML</text>
    </svg>
  </div>
</body>
</html>
```